Website design with eCommerce for revolutionary new product in the manufacturing industry.

We need a website designed for a precision manufacturing company based in the suburbs of Minneapolis, Minnesota called Velkrin Manufacturing. We have a revolutionary new product, the TARN LOCK, to introduce and sell through an eCommerce storefront. The website would include company information, product information, and the storefront. Green is a color that represents Velkrin Manufacturing. The final design should communicate that we exclusively offer premium products at a premium price. The design should also let the customer know they are the focus of our work.

Target Market(s)

Machinists and machine shops

Industry/Entity Type

Manufacturing and machine shops

Coding

Coded - Design and coding required

Font styles to use
Sans Serif

Colors
59FF00
82FF00
B8FF75
E3FFCB
F4FFEA

Requirements
Must have
• eCommerce storefront, Made in USA references
Nice to have
• Home page, TARN LOCK Product page, About Us, Capabilities, Contact, etc.
Should not have
• Should not be too much text and reading.

```html
<!DOCTYPE html>
<html lang="en">
<head>
<meta charset="utf-8">
<title>Contact – TARN LOCK</title>
<link href="https://fonts.googleapis.com/css2?family=Audiowide&family=Poppins:wght@400;500;600;700&display=swap" rel="stylesheet">
<style>
:root{
  --green:#59ff00;
  --page:#141414;
  --footer:#1b1b1b;
  --field:#2a2a2a;
  --white:#ffffff;
  --muted:#d6d6d6;
  --display:'Audiowide',sans-serif;
  --body:'Poppins',sans-serif;
}
*{margin:0;padding:0;box-sizing:border-box}
html,body{width:672px;height:1200px;overflow:hidden;background:var(--page);font-family:var(--body);color:var(--white)}
.canvas{position:relative;width:672px;height:1200px;overflow:hidden}
.abs{position:absolute}

/* header */
.site-header{position:absolute;left:0;top:0;width:672px;height:43px;background:#141414;z-index:3}
.brand{position:absolute;font-family:var(--display);color:var(--white);white-space:nowrap;letter-spacing:.5px}
.site-header .brand{left:50px;top:12px;font-size:15px;line-height:18px}
.main-nav{position:absolute;left:178px;top:17px;display:flex;gap:11px;font-size:6.6px;font-weight:600;letter-spacing:.1px}
.nav-cta{position:absolute;right:0;top:0;width:59px;height:43px;background:var(--green);color:#111;font-size:7px;font-weight:700;display:flex;align-items:center;justify-content:center}

/* hero */
.hero{position:absolute;left:0;top:0;width:672px;height:262px}
.hero-title{position:absolute;left:0;width:672px;top:110px;text-align:center;font-family:var(--display);font-size:35px;line-height:40px;letter-spacing:1px}

/* intro */
.section-title{position:absolute;left:0;width:672px;top:276px;text-align:center;font-family:var(--display);font-size:20px;line-height:24px;letter-spacing:.5px}
.title-rule{position:absolute;left:313px;top:306px;width:47px;height:2px;background:var(--green)}
.intro{position:absolute;left:0;width:672px;top:320px;text-align:center;font-size:8.4px}

/* contact details */
.detail{position:absolute;left:110px;display:flex;align-items:center;gap:9px}
.detail-icon{width:37px;height:37px;background:var(--green);border-radius:3px;display:flex;align-items:center;justify-content:center}
.detail-label{font-size:11px;line-height:13px;color:var(--muted)}
.detail-value{font-size:12.5px;line-height:15px;font-weight:700;color:var(--muted)}

/* form */
.field-label{position:absolute;font-size:6.2px;font-weight:700;letter-spacing:.2px}
.field{position:absolute;background:var(--field);border-radius:2px;font-size:6.8px;color:#d8d8d8;padding-left:8px;display:flex;align-items:center}
.field.area{align-items:flex-start;padding-top:8px}
.submit-btn{position:absolute;left:337px;top:535px;width:225px;height:26px;background:var(--green);border-radius:2px;color:#111;font-size:8.6px;font-weight:700;display:flex;align-items:center;justify-content:center}
.submit-btn svg{position:absolute;right:10px;top:8px}

/* map */
.map-frame{position:absolute;left:105px;top:616px;width:462px;height:212px;background:#2a2a2a;border-radius:4px}
.map-area{position:absolute;left:4px;top:5px;width:454px;height:202px;border-radius:3px;background:linear-gradient(135deg,#e6e6e6,#d2d2d2)}

/* footer */
.footer{position:absolute;left:0;top:889px;width:672px;height:311px;background:var(--footer)}
.footer .brand{left:50px;top:30px;font-size:16px;line-height:20px}
.footer-blurb{position:absolute;left:198px;top:28px;font-size:8.4px;line-height:12.5px;color:#e2e2e2}
.callout{position:absolute;left:0;top:0}
.call-icon{position:absolute;left:441px;top:33px;width:25px;height:25px;background:#111;border-radius:2px;display:flex;align-items:center;justify-content:center}
.call-text{position:absolute;left:473px;top:34px;color:#111;font-weight:600;font-size:7.4px;line-height:24px;white-space:nowrap}
.call-text strong{font-size:15px;font-weight:700;margin-left:3px;letter-spacing:.3px}
.col-title{position:absolute;top:116px;font-family:var(--display);font-size:9.3px;letter-spacing:.3px}
.link-list{position:absolute;left:81px;top:135px;list-style:none;font-size:6.9px;line-height:12.5px}
.social{position:absolute;left:208px;display:flex;align-items:center;gap:4px;font-size:6.9px}
.social i{display:block;width:13px;height:13px;background:#2c2c2c;border-radius:1px;position:relative}
.social i::after{content:"";position:absolute;left:5px;top:5px;width:3px;height:3px;background:#ddd}
.contact-item{position:absolute;left:314px;font-size:7px;line-height:11px}
.contact-item svg{position:absolute;left:0;top:1px}
.contact-item span{display:block;margin-left:12px}
.mini-field{position:absolute;left:449px;width:146px;height:19px;background:#2b2b2b;font-size:6.8px;color:#ddd;padding-left:8px;display:flex;align-items:center}
.mini-submit{position:absolute;left:449px;top:211px;width:51px;height:20px;background:var(--white);color:#111;font-size:7px;font-weight:700;display:flex;align-items:center;justify-content:center;border-radius:1px}
.footer-rule{position:absolute;left:50px;top:273px;width:572px;height:1px;background:#333}
.copyright{position:absolute;left:0;width:672px;top:286px;text-align:center;font-size:7.3px;font-weight:700}
.to-top{position:absolute;left:633px;top:262px;width:26px;height:25px;background:var(--green);display:flex;align-items:center;justify-content:center}
</style>
</head>
<body>
<div class="canvas">

  <svg class="hero" viewBox="0 0 672 262" width="672" height="262">
    <defs>
      <linearGradient id="steel" x1="0" y1="0" x2="1" y2="1">
        <stop offset="0" stop-color="#6b6862"/>
        <stop offset=".5" stop-color="#3d3b37"/>
        <stop offset="1" stop-color="#57524a"/>
      </linearGradient>
    </defs>
    <polygon points="0,43 672,43 672,157 10,259 0,260" fill="url(#steel)" role="img" aria-label="Photo of machined steel parts laid out in rows"/>
    <polygon points="10,259 672,157 672,185 0,261" fill="#59ff00"/>
  </svg>

  <header class="site-header">
    <div class="brand">TARN LOCK</div>
    <nav class="main-nav">
      <span>WHY VELKRIN MANUFACTURING?</span><span>WHAT WE DO</span><span>HOW WE MAKE IT BETTER</span><span>CAPABILITIES</span><span>GALLERY</span><span>ABOUT US</span><span>WISDOM</span>
    </nav>
    <div class="nav-cta">CONTACT</div>
  </header>

  <h1 class="hero-title">CONTACT</h1>

  <h2 class="section-title">GET IN TOUCH</h2>
  <div class="title-rule"></div>
  <p class="intro">Please fill out the information below to complete...</p>

  <div class="detail" style="top:366px">
    <div class="detail-icon"><svg width="16" height="16" viewBox="0 0 24 24"><path d="M6.6 10.8a15 15 0 0 0 6.6 6.6l2.2-2.2c.3-.3.7-.4 1-.2 1.1.4 2.3.6 3.6.6.6 0 1 .4 1 1V20c0 .6-.4 1-1 1C10.6 21 3 13.4 3 4c0-.6.4-1 1-1h3.5c.6 0 1 .4 1 1 0 1.3.2 2.5.6 3.6.1.3 0 .7-.2 1z" fill="#111"/></svg></div>
    <div><div class="detail-label">Phone:</div><div class="detail-value">123 4567 655</div></div>
  </div>
  <div class="detail" style="top:418px">
    <div class="detail-icon"><svg width="16" height="12" viewBox="0 0 16 12"><rect x="0" y="0" width="16" height="12" rx="1.5" fill="#111"/><path d="M1 1.5 8 6.5 15 1.5" stroke="#59ff00" stroke-width="1.3" fill="none"/></svg></div>
    <div><div class="detail-label">Email:</div><div class="detail-value">info@tarnlock.com</div></div>
  </div>
  <div class="detail" style="top:470px">
    <div class="detail-icon"><svg width="14" height="18" viewBox="0 0 14 18"><path d="M7 0a7 7 0 0 0-7 7c0 5 7 11 7 11s7-6 7-11a7 7 0 0 0-7-7z" fill="#111"/><circle cx="7" cy="7" r="2.6" fill="#59ff00"/></svg></div>
    <div><div class="detail-label">Address:</div><div class="detail-value">Some goes address here</div></div>
  </div>

  <form>
    <div class="field-label" style="left:335px;top:366px">NAME*</div>
    <div class="field-label" style="left:451px;top:366px">EMAIL*</div>
    <div class="field" style="left:337px;top:376px;width:111px;height:23px">Enter your name</div>
    <div class="field" style="left:451px;top:376px;width:111px;height:23px">Enter your email</div>
    <div class="field-label" style="left:335px;top:405px">PHONE*</div>
    <div class="field-label" style="left:451px;top:405px">DATE*</div>
    <div class="field" style="left:337px;top:415px;width:111px;height:23px">Enter phone number</div>
    <div class="field" style="left:451px;top:415px;width:111px;height:23px">Select date
      <svg style="position:absolute;right:9px;top:9px" width="6" height="4" viewBox="0 0 6 4"><path d="M.5.5 3 3 5.5.5" stroke="#59ff00" fill="none"/></svg></div>
    <div class="field-label" style="left:335px;top:446px">PHONE*</div>
    <div class="field area" style="left:337px;top:456px;width:225px;height:63px">Type your text...</div>
    <div class="submit-btn">SUBMIT NOW
      <svg width="11" height="10" viewBox="0 0 11 10"><path d="M0 4.5 11 0 8.5 10 5.5 6.5 10 1 4 5.5z" fill="#111"/></svg></div>
  </form>

  <div class="map-frame">
    <div class="map-area" role="img" aria-label="Street map showing the company location">
      <svg style="position:absolute;left:221px;top:89px" width="18" height="24" viewBox="0 0 14 18"><path d="M7 0a7 7 0 0 0-7 7c0 5 7 11 7 11s7-6 7-11a7 7 0 0 0-7-7z" fill="#111"/><circle cx="7" cy="7" r="2.4" fill="#ddd"/></svg>
    </div>
  </div>

  <footer class="footer">
    <svg class="callout" width="672" height="70" viewBox="0 0 672 70">
      <polygon points="0,0 361,0 391,70 0,70" fill="#141414"/>
      <polygon points="369,20 672,20 672,70 391,70" fill="#59ff00"/>
    </svg>
    <div class="brand">TARN LOCK</div>
    <p class="footer-blurb">Velkrin Manufacturing has humble<br>roots, starting as many machine</p>
    <div class="call-icon"><svg width="11" height="11" viewBox="0 0 24 24"><path d="M6.6 10.8a15 15 0 0 0 6.6 6.6l2.2-2.2c.3-.3.7-.4 1-.2 1.1.4 2.3.6 3.6.6.6 0 1 .4 1 1V20c0 .6-.4 1-1 1C10.6 21 3 13.4 3 4c0-.6.4-1 1-1h3.5c.6 0 1 .4 1 1 0 1.3.2 2.5.6 3.6.1.3 0 .7-.2 1z" fill="#fff"/></svg></div>
    <div class="call-text">Call us: <strong>+123 456 7890</strong></div>

    <div class="col-title" style="left:81px">HELPFUL LINKS</div>
    <div class="col-title" style="left:210px">INFORMATION</div>
    <div class="col-title" style="left:314px">CONTACT US</div>
    <div class="col-title" style="left:448px">GET IN TOUCH</div>

    <ul class="link-list">
      <li>Why velkrin manufacturing?</li><li>What We Do</li><li>How We Make It Better</li><li>Capabilities</li><li>Gallery</li><li>About Us</li><li>Wisdom</li><li>Contact Us</li>
    </ul>

    <div class="social" style="top:144px"><i></i>Chatterly</div>
    <div class="social" style="top:164px"><i></i>Pingbird</div>
    <div class="social" style="top:183px"><i></i>Searchly</div>
    <div class="social" style="top:204px"><i></i>Workline</div>
    <div class="social" style="top:224px"><i></i>Clipcast</div>

    <div class="contact-item" style="top:140px">
      <svg width="8" height="6" viewBox="0 0 16 12"><rect width="16" height="12" rx="1.5" fill="#59ff00"/><path d="M1 1.5 8 6.5 15 1.5" stroke="#1b1b1b" stroke-width="1.5" fill="none"/></svg>
      <span>Email:</span><span>info@tarnlock.com</span></div>
    <div class="contact-item" style="top:170px">
      <svg width="8" height="8" viewBox="0 0 24 24"><path d="M6.6 10.8a15 15 0 0 0 6.6 6.6l2.2-2.2c.3-.3.7-.4 1-.2 1.1.4 2.3.6 3.6.6.6 0 1 .4 1 1V20c0 .6-.4 1-1 1C10.6 21 3 13.4 3 4c0-.6.4-1 1-1h3.5c.6 0 1 .4 1 1 0 1.3.2 2.5.6 3.6.1.3 0 .7-.2 1z" fill="#59ff00"/></svg>
      <span>Phone:</span><span>+08 123 456 7890</span></div>
    <div class="contact-item" style="top:199px">
      <svg width="6" height="8" viewBox="0 0 14 18"><path d="M7 0a7 7 0 0 0-7 7c0 5 7 11 7 11s7-6 7-11a7 7 0 0 0-7-7z" fill="#59ff00"/></svg>
      <span>Location:</span><span>Some address line goes</span><span>here city name</span></div>

    <div class="mini-field" style="top:139px">Enter Name</div>
    <div class="mini-field" style="top:162px">Enter Company</div>
    <div class="mini-field" style="top:185px">Enter Country</div>
    <div class="mini-submit">SUBMIT</div>

    <div class="to-top"><svg width="6" height="9" viewBox="0 0 6 9"><path d="M3 9V1M.5 3.5 3 1l2.5 2.5" stroke="#111" fill="none" stroke-width=".8"/></svg></div>
    <div class="footer-rule"></div>
    <p class="copyright">©COPYRIGHT 2022 TARN LOCK, ALL RIGHTS RESERVED</p>
  </footer>
</div>
</body>
</html>
```